Brightwave Reach - Business Card

We need a business card for a Social Media Marketing company that specializes in online marketing for small businesses in Canada using common Social Media platforms such as Pixlora, Chatterly, Blinkpost & Quibber.

I have uploaded a copy of our logo which I would like utilized in the business card. We would like the business card to be modern yet classy design.

Our website is www.brightwavereach.ca

Industry/Entity Type

Marketing

Contact Information for Business Card

Email: info@brightwavereach.ca
Website: www.brightwavereach.ca
Telephone: 604-555-0193

Colors

Designer to choose colors to be used in the design.

Requirements
Must have
• Social Media icons on reverse
• Please add some designs with color.

```html
<!DOCTYPE html>
<html lang="en">
<head>
<meta charset="utf-8">
<title>Brightwave Reach – Business Card</title>
<link rel="stylesheet" href="https://fonts.googleapis.com/css2?family=Open+Sans:wght@400;600;800&display=swap">
<style>
  :root {
    --stage: #000000;
    --card: #2f3034;
    --ink: #ffffff;
    --ink-soft: #d6d6d8;
    --divider: #3d3e43;
  }
  * { margin: 0; padding: 0; box-sizing: border-box; }
  html, body { width: 1200px; height: 900px; overflow: hidden; background: var(--stage); }
  body { position: relative; font-family: "Open Sans", Arial, sans-serif; color: var(--ink); }

  .card {
    position: absolute;
    top: 271px;
    width: 457px;
    height: 281px;
    background: var(--card);
    border-radius: 12px;
  }
  .card--front { left: 137px; }
  .card--back { left: 626px; }

  .brand {
    position: absolute;
    display: flex;
    align-items: center;
    gap: 8px;
    font-weight: 800;
    text-transform: uppercase;
    color: var(--ink);
    line-height: 1;
    text-align: center;
  }
  .brand__square { background: var(--ink); flex: none; }
  .brand__name span { display: block; }

  .card--front .brand { left: 34px; top: 113px; font-size: 20px; }
  .card--front .brand__square { width: 10px; height: 10px; }
  .card--front .brand__name span + span { margin-top: 3px; }

  .card--back .brand { left: 50%; top: 50%; transform: translate(-50%, -50%); font-size: 30px; gap: 12px; }
  .card--back .brand__square { width: 14px; height: 14px; }
  .card--back .brand__name span + span { margin-top: 4px; }

  .divider {
    position: absolute;
    left: 227px;
    top: 80px;
    width: 1px;
    height: 120px;
    background: var(--divider);
  }

  .person { position: absolute; left: 253px; top: 88px; }
  .person__name { font-size: 16px; font-weight: 600; line-height: 1.2; }
  .person__role { font-size: 12px; color: var(--ink-soft); line-height: 1.3; }

  .contact { position: absolute; left: 254px; top: 142px; list-style: none; }
  .contact li {
    display: flex;
    align-items: center;
    gap: 7px;
    font-size: 12.5px;
    color: var(--ink-soft);
    height: 19px;
  }
  .contact svg { width: 9px; height: 9px; fill: var(--ink-soft); flex: none; }
</style>
</head>
<body>

<section class="card card--front" aria-label="Business card front">
  <div class="brand">
    <div class="brand__square"></div>
    <div class="brand__name"><span>Brightwave</span><span>Reach</span></div>
  </div>
  <div class="divider"></div>
  <div class="person">
    <p class="person__name">Daniel Mercer</p>
    <p class="person__role">Managing Director</p>
  </div>
  <ul class="contact">
    <li>
      <svg viewBox="0 0 10 10"><path d="M2 0.5 L3.6 2.6 L2.8 3.6 C3.4 5 4.9 6.5 6.4 7.2 L7.4 6.4 L9.5 8 L8.6 9.5 C4.5 9.5 0.5 5.5 0.5 1.4 Z"/></svg>
      604-555-0193
    </li>
    <li>
      <svg viewBox="0 0 10 10"><path d="M0.5 2 H9.5 V8.5 H0.5 Z M1 2.4 L5 5.4 L9 2.4" stroke="#2f3034" stroke-width="0.8"/></svg>
      info@brightwavereach.ca
    </li>
    <li>
      <svg viewBox="0 0 10 10"><circle cx="5" cy="5" r="4.5"/><path d="M5 0.5 V9.5 M0.5 5 H9.5 M2.4 1.8 C4 4 4 6 2.4 8.2 M7.6 1.8 C6 4 6 6 7.6 8.2" stroke="#2f3034" stroke-width="0.7" fill="none"/></svg>
      www.brightwavereach.ca
    </li>
  </ul>
</section>

<section class="card card--back" aria-label="Business card back">
  <div class="brand">
    <div class="brand__square"></div>
    <div class="brand__name"><span>Brightwave</span><span>Reach</span></div>
  </div>
</section>

</body>
</html>
```